RB Halden Electric Yard Sign

Looking to have a yard sign designed that we can place at projects we are working on. Most likely will be 18" H x 24" W but flexible that we can increase the size if necessary. It should include our logo, our phone # 609-555-0147, website rbhaldenelectric.example and slogan, built on integrity, driven by excellence. Colors should match our brand.

```html
<!DOCTYPE html>
<html lang="en">
<head>
<meta charset="utf-8">
<title>RB Halden Electric Yard Sign</title>
<link rel="stylesheet" href="https://fonts.googleapis.com/css2?family=Barlow+Condensed:wght@700&family=Montserrat:wght@800&family=Nunito:wght@800;900&display=swap">
<style>
  :root {
    --navy: #04356b;
    --red: #ee1b2b;
    --white: #ffffff;
    --backdrop: #e8ebef;
  }
  * { margin: 0; padding: 0; box-sizing: border-box; }
  html, body {
    width: 1200px;
    height: 1029px;
    overflow: hidden;
    background: var(--backdrop);
  }
  .yard-sign {
    position: absolute;
    left: 20px;
    top: 79px;
    width: 1160px;
    height: 871px;
    background: var(--white);
    box-shadow: 0 6px 24px rgba(0, 0, 0, 0.12);
  }
  .sign-frame {
    position: absolute;
    left: 31px;
    top: 31px;
    right: 31px;
    bottom: 31px;
    border: 11px solid var(--navy);
    overflow: hidden;
  }
  .brand-block {
    position: absolute;
    left: 0;
    right: 0;
    top: 0;
    height: 408px;
  }
  .brand-dot {
    position: absolute;
    left: 50%;
    top: 46px;
    width: 96px;
    height: 96px;
    margin-left: -48px;
    border-radius: 50%;
    background: var(--red);
  }
  .brand-name {
    position: absolute;
    left: 0;
    right: 0;
    top: 206px;
    text-align: center;
    font-family: "Montserrat", sans-serif;
    font-weight: 800;
    font-size: 78px;
    line-height: 1;
    letter-spacing: 8px;
    color: var(--red);
  }
  .brand-descriptor {
    position: absolute;
    left: 0;
    right: 0;
    top: 311px;
    text-align: center;
    font-family: "Montserrat", sans-serif;
    font-weight: 800;
    font-size: 40px;
    line-height: 1;
    letter-spacing: 11px;
    color: var(--navy);
  }
  .brand-rule {
    position: absolute;
    left: 84px;
    top: 360px;
    width: 936px;
    height: 12px;
  }
  .slogan-band {
    position: absolute;
    left: 0;
    right: 0;
    top: 408px;
    height: 132px;
    background: var(--red);
    display: flex;
    align-items: center;
    justify-content: center;
  }
  .slogan {
    font-family: "Barlow Condensed", sans-serif;
    font-weight: 700;
    font-size: 64px;
    line-height: 1;
    color: var(--white);
  }
  .contact-band {
    position: absolute;
    left: 0;
    right: 0;
    top: 540px;
    bottom: 0;
    background: var(--navy);
  }
  .phone-line {
    position: absolute;
    left: 0;
    right: 0;
    top: 22px;
    display: flex;
    align-items: center;
    justify-content: center;
    gap: 26px;
  }
  .phone-icon {
    width: 104px;
    height: 104px;
    flex: none;
  }
  .phone-number {
    font-family: "Nunito", sans-serif;
    font-weight: 900;
    font-size: 132px;
    line-height: 1;
    color: var(--white);
    letter-spacing: 1px;
  }
  .website {
    position: absolute;
    left: 0;
    right: 0;
    top: 154px;
    text-align: center;
    font-family: "Nunito", sans-serif;
    font-weight: 800;
    font-size: 54px;
    line-height: 1;
    color: var(--white);
  }
</style>
</head>
<body>
  <main class="yard-sign">
    <div class="sign-frame">
      <section class="brand-block">
        <div class="brand-dot"></div>
        <h1 class="brand-name">R.B. HALDEN</h1>
        <p class="brand-descriptor">Electrical Contractor</p>
        <svg class="brand-rule" viewBox="0 0 936 12" aria-hidden="true">
          <polygon points="0,0 936,0 918,6 18,6" fill="#ee1b2b"/>
          <rect x="18" y="6" width="900" height="6" fill="#04356b"/>
        </svg>
      </section>

      <section class="slogan-band">
        <p class="slogan">Built on Integrity, Driven by Excellence</p>
      </section>

      <section class="contact-band">
        <div class="phone-line">
          <svg class="phone-icon" viewBox="0 0 100 100" aria-hidden="true">
            <circle cx="50" cy="50" r="50" fill="#ffffff"/>
            <path d="M30 24c3-2 6-2 8 1l6 9c2 3 1 6-1 8l-4 3c2 6 8 13 14 16l3-4c2-2 5-3 8-1l9 6c3 2 3 5 1 8l-4 5c-3 3-8 4-12 2-15-6-27-19-33-34-2-4-1-9 2-12z" fill="#04356b"/>
            <path d="M56 30a16 16 0 0 1 14 14" stroke="#04356b" stroke-width="5" fill="none" stroke-linecap="round"/>
            <path d="M57 19a27 27 0 0 1 24 24" stroke="#04356b" stroke-width="5" fill="none" stroke-linecap="round"/>
          </svg>
          <span class="phone-number">609-555-0147</span>
        </div>
        <p class="website">www.rbhaldenelectric.example</p>
      </section>
    </div>
  </main>
</body>
</html>
```